Banner to be displayed at local Farmers Market Booth.

Graphic Design Brief: Farmers Market Banner Contest

Project Overview:We are seeking talented graphic designers to create a visually appealing banner for our booth at the local farmers market. Our company specializes in healthy, all-natural dog and cat treats, and we want a banner that captures our brand identity while drawing in pet owners who value quality and nutrition for their furry friends.

Banner Specifications:

Size: 24 inches x 60 inches (Horizontal orientation) 24" High X 60 wide

Theme: Vintage/Retro

Style: Warm, inviting, nostalgic with a touch of rustic charm

Colors: Earthy, muted tones such as warm browns, soft greens, and creamy yellows. Pops of red or blue may be used sparingly for accents. OR Black and White with gray scales. Would like to see both

Typography: Retro-style fonts that are readable and align with the vintage aesthetic.

Key Elements to Include: website (www.moltbyfarms.com)

Company Name: Moltby Farms

Tagline: " Simply Honest Bites "
Imagery: Illustrations or stylized graphics of happy dogs and cats, possibly interacting with treats.

Emphasis on Natural Ingredients: Icons or design elements that subtly suggest freshness and quality (e.g., leaves, wheat, bones, or paw prints).

Farmers Market Appeal: A design that blends well with the artisanal, handmade, and farm-fresh atmosphere of the market.

Design Considerations:

The banner should be easily readable from a distance.

A balanced composition that doesn't feel overcrowded.

Should evoke trust and warmth while maintaining a professional look.

Avoid overly modern or sleek elements that don’t align with the vintage aesthetic.

Submission Requirements:

High-resolution digital file in PDF or AI format.

CMYK color mode for printing purposes.

Must include a mockup or preview of how it would look in a real farmers market setting.

We look forward to seeing your creative interpretations of our brand! If you have any questions, feel free to reach out.

Font styles to use
Other font styles liked:
• See attachement

Requirements
Nice to have
• Retro/Vintage,playful BUT NOT whimsical

```html
<!DOCTYPE html>
<html lang="en">
<head>
<meta charset="utf-8">
<title>Moltby Farms – Market Banner</title>
<link rel="stylesheet" href="https://fonts.googleapis.com/css2?family=Rye&family=Yesteryear&family=Lilita+One&display=swap">
<style>
  :root {
    --page: #ffffff;
    --cream: #ece5d8;
    --cream-edge: #d9ccb5;
    --rust: #8a3f1e;
    --rust-dark: #5e2610;
    --ink: #1f1f1f;
    --accent-red: #c8392f;
    --circle-red: #d24a3e;
    --grommet: #9a9a9a;
    --fur-light: #d9a866;
    --fur-dark: #9c6a35;
  }
  * { box-sizing: border-box; margin: 0; padding: 0; }
  html, body {
    width: 1200px;
    height: 562px;
    overflow: hidden;
    background: var(--page);
  }
  .banner {
    position: absolute;
    left: 70px;
    top: 70px;
    width: 1060px;
    height: 420px;
    background:
      radial-gradient(ellipse at 45% 50%, var(--cream) 55%, var(--cream-edge) 88%, #b98d63 100%);
    border: 4px solid var(--rust);
    box-shadow: inset 0 0 14px 4px rgba(120, 55, 20, .75), 0 4px 16px rgba(0,0,0,.25);
    overflow: hidden;
  }
  .grommet {
    position: absolute;
    width: 13px;
    height: 13px;
    border-radius: 50%;
    background: var(--grommet);
    box-shadow: inset 0 1px 2px rgba(0,0,0,.4);
  }
  .grommet.tl { left: 10px; top: 10px; }
  .grommet.tr { right: 10px; top: 10px; }
  .grommet.bl { left: 10px; bottom: 10px; }
  .grommet.br { right: 10px; bottom: 10px; }

  .brand-name {
    position: absolute;
    left: 270px;
    top: 44px;
    width: 150px;
    text-align: center;
    font-family: "Yesteryear", cursive;
    font-size: 30px;
    color: var(--ink);
    line-height: 1;
  }
  .headline {
    position: absolute;
    left: 62px;
    top: 100px;
    width: 580px;
    height: 130px;
    overflow: visible;
  }
  .headline text {
    font-family: "Rye", serif;
    font-size: 96px;
    fill: var(--ink);
  }
  .tagline-script {
    position: absolute;
    left: 200px;
    top: 195px;
    width: 300px;
    text-align: center;
    font-family: "Yesteryear", cursive;
    font-size: 118px;
    line-height: 1.1;
    color: var(--ink);
    text-shadow: 2px 3px 0 rgba(255,255,255,.6);
  }
  .web-plate {
    position: absolute;
    left: 78px;
    top: 346px;
    width: 548px;
    height: 60px;
    border-radius: 16px;
    background: var(--accent-red);
    box-shadow: 0 0 0 4px rgba(236,229,216,.9);
    display: flex;
    align-items: center;
    justify-content: center;
    font-family: "Lilita One", sans-serif;
    font-size: 46px;
    letter-spacing: 1px;
    color: var(--ink);
  }
  .sun-disc {
    position: absolute;
    left: 676px;
    top: 32px;
    width: 344px;
    height: 344px;
    border-radius: 50%;
    background: var(--circle-red);
  }
  .pet-portrait {
    position: absolute;
    left: 666px;
    top: 102px;
    width: 364px;
    height: 318px;
    border-radius: 120px 120px 20px 20px;
    background: linear-gradient(160deg, var(--fur-light) 0%, #c8945a 55%, var(--fur-dark) 100%);
  }
</style>
</head>
<body>
  <main class="banner">
    <span class="grommet tl"></span>
    <span class="grommet tr"></span>
    <span class="grommet bl"></span>
    <span class="grommet br"></span>

    <div class="brand-name">Moltby Farms</div>

    <svg class="headline" viewBox="0 0 580 130" aria-label="Simply Honest">
      <text x="0" y="110" textLength="580" lengthAdjust="spacingAndGlyphs">SIMPLY HONEST</text>
    </svg>

    <div class="tagline-script">Bites</div>

    <div class="web-plate">moltbyfarms.com</div>

    <div class="sun-disc"></div>
    <div class="pet-portrait" role="img" aria-label="Illustration of a golden retriever lying behind a calico cat"></div>
  </main>
</body>
</html>
```